Brightway Haus Inc. Business Card Design

Brightway Haus Inc. is in search of a great clean design for our business cards!

Looking to incorporate our full logo and watermark on side one (however, I am open to having the text and watermark separated within the design.)

On side two, I am looking to have contact information (Name, Position, Phone #, Email, Website (www.thebrightwayhaus.ca). Can have the logo and/or watermark as part of the design if applicable.

Please add tagline "Where Shine Counts" on either side 1 or 2. This tagline can be in a sans serif, serif or cursive font as long as it compliments overall design. Capitalization can be title or sentence case depending on how it fits within the design.

Get creative!! Looking for a clean, crisp, premium design! Looking for a glossy card finish with spot UV features when printed. Cards will also be printed with rounded corners. Standard dimensions (3.5 x 2).

Target Market(s)

B2B - primary clients are business owners or property management corporations. (residential jobs are few and far between)

Industry/Entity Type

Business

Contact Information for Business Card

- clean, crisp design
- double sided
- spot UV accents and glossy finish upon printing
- standard business card size (3.5 x 2) with rounded corners
- please see project description for requirements per side

Font styles to use
Sans Serif

Requirements
Must have
• - adequate bleeds with print ready files
• - cohesive design elements between side 1 & 2
• - spot UV elements (can be on both sides or just one, use your discretion)
• - colour pallet should match the logo file provided
• - incorporate tagline "where shine counts" (this tagline can be in a serif or sans serif font as long as it is complimentary to the overall design.
Nice to have
• - Premium elements with a clean design
Should not have
• - Please omit cartoon or whimsical like designs, think premium.
• - Colours should not stray from the pallet of the provided logo.

```html
<!DOCTYPE html>
<html lang="en">
<head>
<meta charset="utf-8">
<title>Brightway Haus Inc. Business Cards</title>
<link rel="stylesheet" href="https://fonts.googleapis.com/css2?family=Roboto:ital,wght@0,400;0,500;0,700;1,400&family=Roboto+Condensed:wght@700&display=swap">
<style>
  :root {
    --backdrop: #2b2b2d;
    --card-white: #f4f4f4;
    --teal: #11b8bc;
    --navy: #1d2758;
    --grey-text: #3f5560;
    --white: #ffffff;
  }
  * { margin: 0; padding: 0; box-sizing: border-box; }
  html, body {
    width: 1200px; height: 960px; overflow: hidden;
    background: var(--backdrop);
    font-family: "Roboto", Arial, sans-serif;
  }
  .canvas { position: relative; width: 1200px; height: 960px; }

  .card {
    position: absolute; left: 320px; width: 600px;
    border-radius: 20px; overflow: hidden;
  }

  /* Side one */
  .card-front { top: 100px; height: 350px; background: var(--card-white); }
  .front-logo {
    position: absolute; top: 152px; left: 0; right: 0;
    display: flex; justify-content: center; align-items: center; gap: 12px;
  }
  .logo-mark { width: 34px; height: 34px; background: var(--teal); }
  .front-logo .logo-name {
    font-family: "Roboto Condensed", "Arial Narrow", sans-serif;
    font-weight: 700; font-size: 46px; letter-spacing: 0.5px;
    color: var(--navy); line-height: 1;
  }
  .tagline {
    position: absolute; top: 284px; left: 0; right: 0;
    display: flex; justify-content: center; align-items: center; gap: 6px;
    font-style: italic; font-size: 18px; color: var(--navy);
  }
  .tagline .accent { color: var(--teal); }
  .tagline-rule { width: 104px; height: 1px; }
  .tagline-rule.left { background: linear-gradient(to right, transparent, var(--navy)); }
  .tagline-rule.right { background: linear-gradient(to left, transparent, var(--navy)); }

  /* Side two */
  .card-back { top: 493px; height: 342px; background: var(--teal); }
  .back-logo {
    position: absolute; top: 36px; left: 29px;
    font-family: "Roboto Condensed", "Arial Narrow", sans-serif;
    font-weight: 700; font-size: 31px; color: var(--white); line-height: 1;
  }
  .contact { position: absolute; top: 118px; left: 29px; }
  .contact-name { font-size: 20px; font-weight: 500; color: var(--white); letter-spacing: 0.3px; }
  .contact-role { font-size: 14.5px; font-weight: 500; color: var(--navy); margin-top: 5px; }
  .contact-address { font-size: 14.5px; color: var(--grey-text); margin-top: 12px; line-height: 19px; }
  .contact-lines { list-style: none; margin-top: 12px; }
  .contact-lines li {
    display: flex; align-items: center; gap: 9px;
    font-size: 14.5px; color: var(--grey-text); line-height: 19px;
  }
  .contact-lines svg { width: 13px; height: 13px; fill: var(--white); flex: none; }
</style>
</head>
<body>
<main class="canvas">

  <section class="card card-front" aria-label="Business card, side one">
    <div class="front-logo">
      <span class="logo-mark" aria-hidden="true"></span>
      <span class="logo-name">BRIGHTWAY HAUS INC.</span>
    </div>
    <p class="tagline">
      <span class="tagline-rule left" aria-hidden="true"></span>
      <span>Where <span class="accent">Shine</span> Counts</span>
      <span class="tagline-rule right" aria-hidden="true"></span>
    </p>
  </section>

  <section class="card card-back" aria-label="Business card, side two">
    <div class="back-logo">BRIGHTWAY HAUS INC.</div>
    <div class="contact">
      <p class="contact-name">DANIEL REYES</p>
      <p class="contact-role">CEO/FOUNDER</p>
      <p class="contact-address">2140 Larkspur Court<br>Juneau, Alaska 99801</p>
      <ul class="contact-lines">
        <li><svg viewBox="0 0 16 16" aria-hidden="true"><path d="M3.5 1l2.5 3-1.5 2c1 2 3 4 5 5l2-1.5 3 2.5-1.5 2.5C7 14 2 9 1 2.5z"/></svg>604 555 0182</li>
        <li><svg viewBox="0 0 16 16" aria-hidden="true"><path d="M4 0h8v16H4zM5.5 2v10h5V2zM7 13.5h2v1H7z" fill-rule="evenodd"/></svg>604 555 0147</li>
        <li><svg viewBox="0 0 16 16" aria-hidden="true"><path d="M4 1h8v4H4zM1 6h14v6h-3v3H4v-3H1zM5 10v4h6v-4z" fill-rule="evenodd"/></svg>604 555 0163</li>
        <li><svg viewBox="0 0 16 16" aria-hidden="true"><path d="M1 3h14v1L8 9 1 4zM1 5.5l7 5 7-5V13H1z"/></svg>hello@brightwayhaus.ca</li>
        <li><svg viewBox="0 0 16 16" aria-hidden="true"><circle cx="8" cy="8" r="7"/></svg>www.thebrightwayhaus.ca</li>
      </ul>
    </div>
  </section>

</main>
</body>
</html>
```